Web design required

1-We need a web design for existing company based in New Zealand
2-We build residential house and light commercial
3-We has in-house designer which allow us can provide interior design
4-We modeling project before site construction, which enable both client and construction team to visually analysis whole project,

Target Market(s)

middle class residential house market
Ref: http://www.parvellbuilders.co.nz/

Industry/Entity Type

Construction Company

Number of Pages Required

1 page

Font styles to use
Sans Serif
Other font styles liked:
• Such as : Central Gothic or similar which has more design taste

Colors

Designer to choose colors to be used in the design.

Requirements
Must have
• Front sheet, contact information, sample project

```html
<!DOCTYPE html>
<html lang="en">
<head>
<meta charset="utf-8">
<title>Kestrel Homes</title>
<link href="https://fonts.googleapis.com/css2?family=Questrial&family=Open+Sans:wght@400;600;700&display=swap" rel="stylesheet">
<style>
:root{
  --brand-blue:#1a5fa8;
  --ink:#222222;
  --muted:#a9a9a9;
  --nav-bg:#333333;
  --footer-bg:#464646;
  --footer-text:#bdbdbd;
  --page-bg:#f4f4f4;
  --white:#ffffff;
  --tile-dark:#2f2f2f;
}
*{margin:0;padding:0;box-sizing:border-box}
html,body{width:1200px;height:2372px;overflow:hidden}
body{position:relative;background:var(--page-bg);font-family:"Questrial",sans-serif;color:var(--ink)}
.abs{position:absolute}

/* Header */
.site-header{left:0;top:0;width:1200px;height:120px;background:var(--white)}
.brand{left:160px;top:34px;display:flex;align-items:center;gap:12px}
.brand-mark{width:50px;height:50px;background:var(--brand-blue)}
.brand-name{font-family:"Questrial",sans-serif;font-size:30px;letter-spacing:4px;color:#4a4a4a;line-height:1}
.header-phone{left:518px;top:44px;display:flex;align-items:center;gap:8px;font-size:25px;color:#555;letter-spacing:1px}
.estimate-label{left:778px;top:52px;font-family:"Open Sans",sans-serif;font-size:13px;color:#555}
.estimate-badge{left:960px;top:21px;width:78px;height:78px;border:2px solid var(--brand-blue);border-radius:50%;display:flex;align-items:center;justify-content:center}
.header-rule{left:160px;top:117px;width:880px;height:3px;background:var(--brand-blue)}

/* Navigation */
.main-nav{left:0;top:120px;width:1200px;height:73px;background:var(--nav-bg)}
.main-nav a{position:absolute;top:29px;font-family:"Open Sans",sans-serif;font-size:12.5px;color:#e6e6e6;text-decoration:none;text-transform:uppercase}

/* Hero */
.hero{left:0;top:193px;width:1200px;height:528px;background:linear-gradient(100deg,#5d5350 0%,#8b8580 25%,#d4d0cb 40%,#7e736e 60%,#5b4f4b 80%,#9b948e 100%)}

/* Welcome */
.welcome{left:0;top:721px;width:1200px;height:378px;background:var(--page-bg)}
.welcome-title{left:0;top:48px;width:1200px;text-align:center;font-family:"Open Sans",sans-serif;font-weight:700;font-size:29px;line-height:40px;color:var(--ink)}
.welcome-title span{color:var(--brand-blue)}
.section-heading{font-size:25px;color:var(--brand-blue)}
.about{left:160px;top:140px;width:490px}
.about p{margin-top:14px;font-family:"Open Sans",sans-serif;font-size:13.5px;line-height:25px;color:var(--muted)}
.what-we-do{left:794px;top:140px}
.what-we-do ul{list-style:none;margin-top:14px}
.what-we-do li{font-family:"Open Sans",sans-serif;font-size:13.5px;line-height:25px;color:var(--muted);padding-left:14px;position:relative}
.what-we-do li::before{content:"";position:absolute;left:0;top:11px;width:5px;height:5px;background:var(--brand-blue)}

/* Services */
.services{left:0;top:1099px;width:1200px;height:514px;background:linear-gradient(180deg,#3d4650 0%,#4e5760 45%,#3a4239 80%,#4a4d45 100%)}
.services-title{left:0;top:66px;width:1200px;text-align:center;font-size:28px;color:var(--white)}
.service-card{top:139px;width:242px;height:305px}
.service-photo{width:242px;height:218px}
.service-label{width:262px;height:87px;background:var(--white);padding:22px 0 0 20px;font-size:18px;line-height:24px;color:#333;clip-path:polygon(0 0,242px 0,262px 50%,242px 100%,0 100%)}
.service-card.last .service-label{width:242px;clip-path:none}

/* Projects */
.projects{left:0;top:1613px;width:1200px;height:390px;background:var(--page-bg)}
.projects-title{left:160px;top:50px;font-size:28px;color:var(--ink)}
.project-card{top:102px;width:205px;height:214px;background:var(--white);box-shadow:0 0 0 1px #e2e2e2}
.project-photo{width:205px;height:166px}
.project-bar{position:absolute;left:0;top:166px;width:205px;height:48px;display:flex;align-items:center;padding-left:15px;font-family:"Open Sans",sans-serif;font-weight:600;font-size:13px;color:#333}
.project-toggle{position:absolute;right:0;top:0;width:50px;height:48px;background:var(--tile-dark);display:flex;align-items:center;justify-content:center}

/* Footer */
.site-footer{left:0;top:2003px;width:1200px;height:369px;background:var(--footer-bg)}
.footer-rule{left:160px;top:0;width:880px;height:8px;background:var(--brand-blue)}
.footer-heading{font-family:"Open Sans",sans-serif;font-size:14px;color:#f0f0f0;text-transform:uppercase}
.footer-col{top:52px}
.footer-col p,.footer-col a{display:block;font-family:"Open Sans",sans-serif;font-size:12px;line-height:22px;color:var(--footer-text);text-decoration:none}
.footer-col .list{margin-top:12px}
.contact-row{display:flex}
.contact-row .key{width:72px;color:#8f8f8f}
.footer-brand{left:160px;top:190px;width:262px;height:88px;background:var(--white);display:flex;align-items:center;justify-content:center;gap:12px}
.copyright{left:798px;top:201px;font-family:"Open Sans",sans-serif;font-size:11.5px;color:#8f8f8f}
.social{top:240px;width:56px;height:56px;border-radius:50%;background:#2c2c2c}
</style>
</head>
<body>

<header class="site-header abs">
  <div class="brand abs">
    <span class="brand-mark"></span>
    <span class="brand-name">KESTREL HOMES</span>
  </div>
  <div class="header-phone abs">
    <svg width="16" height="26" viewBox="0 0 16 26" aria-hidden="true"><path d="M5 2 L9 2 L9 8 L6 9 Q5 13 6 17 L9 18 L9 24 L5 24 Q1 19 1 13 Q1 7 5 2 Z" fill="var(--brand-blue)"/></svg>
    <span>09 555 0142</span>
  </div>
  <div class="estimate-label abs">REQUEST FREE ESTIMATE</div>
  <div class="estimate-badge abs">
    <svg width="40" height="40" viewBox="0 0 40 40" aria-hidden="true">
      <rect x="8" y="6" width="24" height="30" rx="2" fill="none" stroke="#333" stroke-width="2"/>
      <rect x="12" y="10" width="16" height="6" fill="#333"/>
      <g fill="#333"><rect x="12" y="20" width="4" height="3"/><rect x="18" y="20" width="4" height="3"/><rect x="24" y="20" width="4" height="3"/><rect x="12" y="26" width="4" height="3"/><rect x="18" y="26" width="4" height="3"/><rect x="24" y="26" width="4" height="3"/></g>
    </svg>
  </div>
  <div class="header-rule abs"></div>
</header>

<nav class="main-nav abs">
  <a href="#" style="left:180px">Home</a>
  <a href="#" style="left:259px">About Us</a>
  <a href="#" style="left:357px">Our Srvices</a>
  <a href="#" style="left:476px">Our Projects</a>
  <a href="#" style="left:605px">Contact Us</a>
</nav>

<div class="hero abs" role="img" aria-label="Interior of a modern bathroom with a sunken bath, tall curtained windows and a glass chandelier"></div>

<section class="welcome abs">
  <h1 class="welcome-title abs">WELCOME TO THE<br><span>KESTREL HOMES</span></h1>
  <div class="about abs">
    <h2 class="section-heading">About Us</h2>
    <p>Kestrel Homes is dedicated to creating and renovating beautiful and unusual buildings.<br>Kestrel Homes works with you to take dream houses off the blueprints and into reality. We have the knowledge and expertise to customise homes to suit you – from unusual materials and designs to environm-entally sensitive locations.</p>
  </div>
  <div class="what-we-do abs">
    <h2 class="section-heading">What We Do</h2>
    <ul>
      <li>Build Residential House</li>
      <li>Light Commercial</li>
      <li>Interior Design</li>
      <li>Modeling Project</li>
      <li>House Designer</li>
    </ul>
  </div>
</section>

<section class="services abs" role="img" aria-label="Background photo of a large two-storey white house at dusk">
  <h2 class="services-title abs">Our Services</h2>
  <div class="service-card abs" style="left:212px">
    <div class="service-photo" role="img" aria-label="Builders reviewing rolled plans on a workbench" style="background:linear-gradient(135deg,#a58a7a,#d9c7b8 60%,#8f7466)"></div>
    <div class="service-label">Preconstruction<br>Planning</div>
  </div>
  <div class="service-card abs" style="left:477px">
    <div class="service-photo" role="img" aria-label="Hand sketching a building in perspective" style="background:linear-gradient(135deg,#f2f2f2,#cfcfcf 60%,#e8e8e8)"></div>
    <div class="service-label">Construction<br>Modelling</div>
  </div>
  <div class="service-card last abs" style="left:746px">
    <div class="service-photo" role="img" aria-label="Site team in hard hats reviewing drawings" style="background:linear-gradient(135deg,#6e6f73,#c9b48a 55%,#e0c24a)"></div>
    <div class="service-label">Full Project<br>Management</div>
  </div>
</section>

<section class="projects abs">
  <h2 class="projects-title abs">Our Projects</h2>

  <article class="project-card abs" style="left:160px">
    <div class="project-photo" role="img" aria-label="Multi-storey building under scaffolding" style="background:linear-gradient(180deg,#7fa6cf,#b9c3cc 50%,#6b7378)"></div>
    <div class="project-bar">Rowan Project
      <span class="project-toggle"><svg width="26" height="22" viewBox="0 0 26 22" aria-hidden="true"><g stroke="#fff" stroke-width="2" fill="none"><path d="M2 4 H14 M2 11 H12 M2 18 H10"/><path d="M20 2 V20 M17 17 L20 20 L23 17"/></g></svg></span>
    </div>
  </article>

  <article class="project-card abs" style="left:386px">
    <div class="project-photo" role="img" aria-label="White weatherboard house near completion" style="background:linear-gradient(180deg,#5f95cf,#e2e2e2 50%,#8a8478)"></div>
    <div class="project-bar">Ashby Project
      <span class="project-toggle"><svg width="26" height="22" viewBox="0 0 26 22" aria-hidden="true"><g stroke="#fff" stroke-width="2" fill="none"><path d="M2 4 H14 M2 11 H12 M2 18 H10"/><path d="M20 2 V20 M17 17 L20 20 L23 17"/></g></svg></span>
    </div>
  </article>

  <article class="project-card abs" style="left:610px">
    <div class="project-photo" role="img" aria-label="Lit two-storey family home at dusk" style="background:linear-gradient(180deg,#2f5fa8,#e8e4da 50%,#a89672)"></div>
    <div class="project-bar">Kowhai Rd Project
      <span class="project-toggle"><svg width="26" height="22" viewBox="0 0 26 22" aria-hidden="true"><g stroke="#fff" stroke-width="2" fill="none"><path d="M2 4 H14 M2 11 H12 M2 18 H10"/><path d="M20 2 V20 M17 17 L20 20 L23 17"/></g></svg></span>
    </div>
  </article>

  <article class="project-card abs" style="left:835px">
    <div class="project-photo" role="img" aria-label="White house with front gate and garden" style="background:linear-gradient(180deg,#4f7fb8,#f0f0f0 50%,#5d6a4c)"></div>
    <div class="project-bar">Elmwood Project
      <span class="project-toggle"><svg width="26" height="22" viewBox="0 0 26 22" aria-hidden="true"><g stroke="#fff" stroke-width="2" fill="none"><path d="M2 4 H14 M2 11 H12 M2 18 H10"/><path d="M20 2 V20 M17 17 L20 20 L23 17"/></g></svg></span>
    </div>
  </article>
</section>

<footer class="site-footer abs">
  <div class="footer-rule abs"></div>
  <div class="footer-col abs" style="left:160px">
    <h3 class="footer-heading">Navigation</h3>
    <div class="list"><a href="#">Home</a><a href="#">Our Service</a><a href="#">Our Projects</a></div>
  </div>
  <div class="footer-col abs" style="left:387px;width:340px">
    <h3 class="footer-heading">Employment</h3>
    <div class="list"><p>To apply for a job with Kestrel Homes, please send a cover letter together with your C.V. to: info@kestrelhome.com</p></div>
  </div>
  <div class="footer-col abs" style="left:798px">
    <h3 class="footer-heading">Contact Us</h3>
    <div class="list">
      <div class="contact-row"><p class="key">Address :</p><p>27 Meadowbank Drive,<br>Eastvale Auckland</p></div>
      <div class="contact-row" style="margin-top:6px"><p class="key">Phone No :</p><p>09 555 0142</p></div>
    </div>
  </div>
  <div class="footer-brand abs">
    <span class="brand-mark"></span>
    <span class="brand-name">KESTREL HOMES</span>
  </div>
  <p class="copyright abs">©2017 Kestrel Homes Allrights are Reserved</p>
  <a class="social abs" href="#" aria-label="Social link" style="left:799px"></a>
  <a class="social abs" href="#" aria-label="Social link" style="left:860px"></a>
  <a class="social abs" href="#" aria-label="Social link" style="left:922px"></a>
  <a class="social abs" href="#" aria-label="Social link" style="left:984px"></a>
</footer>

</body>
</html>
```